Sales sheet for printing and embroidery apparel items - Copper Hollow Graphics

I would like a one page flyer or sales sheet that I would use as a template to send different images of apparel we produce. I have attached examples of layouts I like.
- Ideally, it would have space for 3-5 items.
- I would like it one page only - not a folding flyer.
- Our companies name is Copper Hollow Graphics.
- This will be used for many different products and markets so I don't need wording/copy. You can use wording from the 7M9 or T58 flyer.

Colors
0054AA
0677BA
7BADD7
CADEEF
E8F1F8
00AB8E
00BBA5
67D7C9
C6EFE9
E9F9F6
FFC000
F8CF3A
FAE287
FDF2CF
FEFAEE

Requirements
Must have
• Places for between 3 and 5 images of apparel (t-shirts, hats etc)

```html
<!DOCTYPE html>
<html lang="en">
<head>
<meta charset="utf-8">
<title>Copper Hollow Graphics – Retreat Apparel Sales Sheet</title>
<link href="https://fonts.googleapis.com/css2?family=Anton&family=Roboto:wght@400;500;700&display=swap" rel="stylesheet">
<style>
  :root {
    --backdrop: #b3b3b3;
    --paper: #ffffff;
    --red: #dc3b3b;
    --bright-blue: #3a87d6;
    --navy: #003b73;
    --ink: #1d1d1d;
    --placeholder: #e1e1e1;
    --tear-shadow: #d9d9d9;
    --photo-light: #e9e9e6;
    --photo-dark: #9a9c9f;
    --logo-orange: #e8674b;
  }
  * { box-sizing: border-box; margin: 0; padding: 0; }
  html, body { width: 906px; height: 1200px; overflow: hidden; }
  body { background: var(--backdrop); font-family: "Roboto", Arial, sans-serif; position: relative; }

  .sheet { position: absolute; left: 63px; top: 15px; width: 780px; height: 1170px; background: var(--paper); overflow: hidden; }
  .abs { position: absolute; }
  .display { font-family: "Anton", "Impact", sans-serif; font-weight: 400; text-transform: uppercase; letter-spacing: 0.5px; }

  /* header */
  .brand { left: 100px; top: 10px; width: 176px; text-align: center; }
  .brand-mark { width: 40px; height: 40px; background: var(--logo-orange); margin: 0 auto 6px; }
  .brand-name { font-family: "Anton", "Impact", sans-serif; color: var(--navy); font-size: 22px; line-height: 24px; text-transform: uppercase; }
  .headline { left: 18px; top: 112px; line-height: 1; }
  .headline span { display: block; }
  .headline .l1 { color: var(--red); font-size: 56px; line-height: 54px; letter-spacing: 1px; }
  .headline .l2 { color: var(--bright-blue); font-size: 56px; line-height: 54px; letter-spacing: 1.2px; }
  .headline .l3 { color: var(--navy); font-size: 44px; line-height: 44px; letter-spacing: 0.6px; }
  .hero-photo { left: 382px; top: 0; width: 398px; height: 253px; background: linear-gradient(135deg, var(--photo-light) 0%, #d7d8d6 55%, var(--photo-dark) 100%); }

  /* bands */
  .band-svg { left: 0; width: 780px; }

  .perks { left: 0; top: 300px; width: 780px; height: 140px; }
  .perk { position: absolute; width: 180px; text-align: center; color: #fff; }
  .perk svg { display: block; margin: 0 auto; }
  .perk h3 { font-family: "Anton", "Impact", sans-serif; font-weight: 400; font-size: 16px; letter-spacing: 0.4px; margin-top: 10px; }
  .perk p { font-size: 11.5px; line-height: 15px; margin-top: 3px; }

  .section-title { left: 0; width: 780px; text-align: center; font-size: 25px; }
  .section-title .red { color: var(--red); }
  .section-title .blue { color: var(--bright-blue); }
  .title-rule { height: 2px; background: var(--navy); }

  .product-slot { top: 532px; width: 140px; height: 148px; background: var(--placeholder); }

  .offer-title { left: 0; top: 752px; width: 780px; text-align: center; color: #fff; font-size: 27px; }
  .offer-item { display: flex; align-items: center; gap: 8px; color: #fff; font-weight: 500; font-size: 13px; line-height: 16px; top: 800px; height: 46px; }
  .offer-divider { top: 790px; width: 1px; height: 70px; background: rgba(255,255,255,0.35); }

  .step { top: 944px; width: 220px; text-align: center; }
  .step h3 { font-family: "Anton", "Impact", sans-serif; font-weight: 400; color: var(--navy); font-size: 16px; letter-spacing: 0.3px; margin-top: 8px; }
  .step p { font-size: 11.5px; line-height: 14.6px; color: var(--ink); margin-top: 4px; }
  .step svg { display: block; margin: 0 auto; }
  .step-arrow { top: 1001px; }

  .cta { left: 30px; top: 1098px; color: var(--navy); font-size: 27px; letter-spacing: 0.4px; }
  .contact { display: flex; align-items: center; gap: 8px; top: 1135px; height: 26px; }
  .contact .dot { width: 26px; height: 26px; border-radius: 50%; background: var(--red); display: flex; align-items: center; justify-content: center; }
  .contact-phone { left: 21px; font-family: "Anton", "Impact", sans-serif; font-size: 23px; color: var(--ink); }
  .contact-email { left: 196px; font-size: 16px; color: var(--ink); }
  .badge { top: 1108px; height: 26px; }
  .social { top: 1141px; width: 18px; height: 18px; border-radius: 50%; background: var(--red); }
</style>
</head>
<body>
<main class="sheet">

  <!-- header -->
  <div class="abs brand">
    <div class="brand-mark"></div>
    <div class="brand-name">Copper Hollow<br>Graphics</div>
  </div>
  <h1 class="abs headline display">
    <span class="l1">Order Shirts</span>
    <span class="l2">For Your All</span>
    <span class="l3">Of Your Retreats</span>
  </h1>
  <div class="abs hero-photo" role="img" aria-label="Photo of branded merchandise laid flat on white wood: striped blanket, notebook, steel bottle, black backpack and grey hoodie"></div>

  <!-- torn strip below header -->
  <svg class="abs band-svg" style="top:248px" height="40" viewBox="0 0 780 40" aria-hidden="true">
    <path d="M0,18 L40,10 L80,20 L120,8 L160,16 L200,6 L240,18 L280,10 L320,16 L360,4 L400,14 L440,8 L480,18 L520,6 L560,16 L600,10 L640,18 L680,8 L720,16 L780,10 L780,40 L0,40 Z" fill="var(--tear-shadow)"/>
    <path d="M0,24 L40,16 L80,26 L120,14 L160,22 L200,12 L240,24 L280,16 L320,22 L360,10 L400,20 L440,14 L480,24 L520,12 L560,22 L600,16 L640,24 L680,14 L720,22 L780,16 L780,40 L0,40 Z" fill="var(--paper)"/>
  </svg>

  <!-- red perks band -->
  <svg class="abs band-svg" style="top:276px" height="210" viewBox="0 0 780 210" aria-hidden="true">
    <path d="M0,20 L40,12 L80,22 L120,10 L160,18 L200,8 L240,20 L280,12 L320,18 L360,6 L400,16 L440,10 L480,20 L520,8 L560,18 L600,12 L640,20 L680,10 L720,18 L780,12
             L780,190 L740,198 L700,186 L660,200 L620,190 L580,198 L540,186 L500,196 L460,188 L420,200 L380,188 L340,196 L300,186 L260,198 L220,190 L180,198 L140,186 L100,196 L60,188 L0,194 Z" fill="var(--red)"/>
    <path d="M0,194 L60,188 L100,196 L140,186 L180,198 L220,190 L260,198 L300,186 L340,196 L380,188 L420,200 L460,188 L500,196 L540,186 L580,198 L620,190 L660,200 L700,186 L740,198 L780,190 L780,202 L700,206 L600,200 L500,208 L400,200 L300,208 L200,200 L100,206 L0,202 Z" fill="var(--tear-shadow)"/>
  </svg>

  <section class="abs perks">
    <div class="perk" style="left:11px;top:10px">
      <svg width="64" height="68" viewBox="0 0 64 68" fill="none" stroke="#fff" stroke-width="2" stroke-linejoin="round">
        <path d="M12,10 L24,4 Q32,10 40,4 L52,10 L58,24 L50,28 L50,44 L14,44 L14,28 L6,24 Z"/>
        <path d="M14,50 L50,50 M14,56 L50,56 M14,62 L50,62"/>
      </svg>
      <h3>Low Minimums</h3>
      <p>Order as few as 24 pieces<br>to get started.</p>
    </div>
    <div class="perk" style="left:204px;top:10px">
      <svg width="64" height="68" viewBox="0 0 64 68" fill="none" stroke="#fff" stroke-width="2" stroke-linejoin="round" stroke-linecap="round">
        <path d="M10,6 L18,8 L30,54 L58,46"/>
        <circle cx="32" cy="60" r="5"/>
        <rect x="30" y="18" width="22" height="22" transform="rotate(-15 41 29)"/>
        <path d="M2,40 L16,40 M4,48 L20,48 M8,56 L22,56"/>
      </svg>
      <h3>Fast Turnaround</h3>
      <p>2-week standard delivery.</p>
    </div>
    <div class="perk" style="left:404px;top:10px">
      <svg width="70" height="68" viewBox="0 0 70 68" fill="none" stroke="#fff" stroke-width="2">
        <circle cx="35" cy="10" r="7"/>
        <circle cx="18" cy="16" r="5"/><circle cx="52" cy="16" r="5"/>
        <path d="M24,60 L24,30 Q35,20 46,30 L46,60"/>
        <path d="M10,56 L10,30 Q16,24 22,28 M60,56 L60,30 Q54,24 48,28"/>
      </svg>
      <h3>Real People</h3>
      <p>Work with our team of<br>experts and artists.</p>
    </div>
    <div class="perk" style="left:593px;top:10px">
      <svg width="64" height="68" viewBox="0 0 64 68" fill="none" stroke="#fff" stroke-width="2" stroke-linejoin="round" stroke-linecap="round">
        <path d="M32,6 L48,12 L48,28 Q48,40 32,48 Q16,40 16,28 L16,12 Z"/>
        <path d="M25,26 L30,32 L40,20"/>
        <path d="M4,52 Q14,46 24,52 L40,54 Q46,56 42,60 L24,60 M42,58 L56,50 Q62,48 60,54 L46,64 L16,64 L4,60"/>
      </svg>
      <h3>Guaranteed</h3>
      <p>We promise accurate,<br>quality work.</p>
    </div>
  </section>

  <!-- products -->
  <h2 class="abs section-title display" style="top:487px"><span class="red">Our</span> <span class="blue">Products</span></h2>
  <div class="abs title-rule" style="left:350px;top:521px;width:80px"></div>
  <div class="abs product-slot" role="img" aria-label="Product photo slot 1" style="left:24px"></div>
  <div class="abs product-slot" role="img" aria-label="Product photo slot 2" style="left:172px"></div>
  <div class="abs product-slot" role="img" aria-label="Product photo slot 3" style="left:320px"></div>
  <div class="abs product-slot" role="img" aria-label="Product photo slot 4" style="left:468px"></div>
  <div class="abs product-slot" role="img" aria-label="Product photo slot 5" style="left:616px"></div>

  <!-- navy offer band -->
  <svg class="abs band-svg" style="top:694px" height="210" viewBox="0 0 780 210" aria-hidden="true">
    <path d="M0,10 L60,4 L100,14 L160,2 L220,12 L280,6 L340,14 L400,4 L460,12 L520,2 L580,14 L640,6 L700,12 L780,0 L780,28 L0,28 Z" fill="var(--tear-shadow)"/>
    <path d="M0,22 L40,14 L80,24 L120,12 L160,20 L200,10 L240,22 L280,14 L320,20 L360,8 L400,18 L440,12 L480,22 L520,10 L560,20 L600,14 L640,22 L680,12 L720,20 L780,14
             L780,178 L740,186 L700,174 L660,188 L620,178 L580,186 L540,174 L500,184 L460,176 L420,188 L380,176 L340,184 L300,174 L260,186 L220,178 L180,186 L140,174 L100,184 L60,176 L0,182 Z" fill="var(--navy)"/>
    <path d="M0,182 L60,176 L100,184 L140,174 L180,186 L220,178 L260,186 L300,174 L340,184 L380,176 L420,188 L460,176 L500,184 L540,174 L580,186 L620,178 L660,188 L700,174 L740,186 L780,178 L780,194 L680,198 L580,192 L480,200 L380,192 L280,200 L180,192 L80,198 L0,192 Z" fill="var(--tear-shadow)"/>
  </svg>

  <h2 class="abs offer-title display">We Offer</h2>
  <div class="abs title-rule" style="left:350px;top:792px;width:80px;background:#fff"></div>

  <div class="abs offer-item" style="left:22px">
    <svg width="48" height="48" viewBox="0 0 48 48" fill="#fff" aria-hidden="true">
      <path d="M24,14 a10,10 0 1,1 -0.01,0 Z M20,4 h8 v6 h-8 Z M20,38 h8 v6 h-8 Z M4,20 h6 v8 h-6 Z M38,20 h6 v8 h-6 Z"/>
      <circle cx="24" cy="24" r="5" fill="var(--navy)"/>
    </svg>
    <span>Art Design</span>
  </div>
  <div class="abs offer-divider" style="left:154px"></div>
  <div class="abs offer-item" style="left:168px">
    <svg width="50" height="34" viewBox="0 0 50 34" aria-hidden="true">
      <rect x="1" y="2" width="32" height="22" rx="3" fill="#fff"/>
      <path d="M34,8 L42,8 L49,16 L49,24 L34,24 Z" fill="#fff"/>
      <circle cx="10" cy="27" r="5" fill="#fff" stroke="var(--navy)" stroke-width="2"/>
      <circle cx="40" cy="27" r="5" fill="#fff" stroke="var(--navy)" stroke-width="2"/>
      <text x="17" y="18" text-anchor="middle" font-family="Anton, Impact, sans-serif" font-size="11" fill="var(--navy)">FREE</text>
    </svg>
    <span>Free Shipping</span>
  </div>
  <div class="abs offer-divider" style="left:323px"></div>
  <div class="abs offer-item" style="left:342px">
    <svg width="40" height="40" viewBox="0 0 40 40" aria-hidden="true">
      <circle cx="24" cy="14" r="12" fill="#fff"/>
      <text x="24" y="20" text-anchor="middle" font-family="Roboto, Arial, sans-serif" font-weight="700" font-size="16" fill="var(--navy)">$</text>
      <rect x="2" y="26" width="6" height="12" fill="#fff"/>
      <path d="M10,28 L20,26 L28,30 L36,26 Q40,26 38,30 L28,38 L10,38 Z" fill="#fff"/>
    </svg>
    <span>We Pay ALL Royalties<br>to the Movement</span>
  </div>
  <div class="abs offer-divider" style="left:539px"></div>
  <div class="abs offer-item" style="left:560px">
    <svg width="44" height="40" viewBox="0 0 44 40" aria-hidden="true">
      <path d="M14,2 L18,2 Q22,6 26,2 L30,2 L42,10 L38,20 L33,18 L33,38 L11,38 L11,18 L6,20 L2,10 Z" fill="#fff"/>
      <path d="M18,2 L22,10 L26,2" fill="none" stroke="var(--navy)" stroke-width="1.5"/>
    </svg>
    <span>Many Options of Shirt<br>Styles and Colors</span>
  </div>

  <!-- how to start -->
  <h2 class="abs section-title display" style="top:897px"><span class="red">How to Start</span> <span class="blue">an Order</span></h2>
  <div class="abs title-rule" style="left:364px;top:931px;width:80px"></div>

  <div class="abs step" style="left:23px">
    <svg width="38" height="40" viewBox="0 0 38 40" fill="none" stroke="var(--red)" stroke-width="2" stroke-linecap="round" aria-hidden="true">
      <circle cx="17" cy="17" r="15"/>
      <path d="M28,28 L36,38"/>
      <path d="M8,20 L10,14 Q11,12 13,12 L21,12 Q23,12 24,14 L26,20 Z M7,20 L27,20 L27,24 L7,24 Z"/>
    </svg>
    <h3>Choose Your Ride</h3>
    <p>Send us a picture, or let us know the make and model of the vehicle you would like featured on your apparel.</p>
  </div>
  <svg class="abs step-arrow" style="left:234px" width="44" height="10" viewBox="0 0 44 10" aria-hidden="true">
    <path d="M0,5 L42,5 M36,1 L42,5 L36,9" fill="none" stroke="var(--ink)" stroke-width="1.4"/>
  </svg>

  <div class="abs step" style="left:283px">
    <svg width="42" height="40" viewBox="0 0 42 40" fill="none" stroke="var(--red)" stroke-width="2" stroke-linejoin="round" aria-hidden="true">
      <path d="M12,2 L17,2 Q21,6 25,2 L30,2 L40,10 L36,18 L31,16 L31,36 L11,36 L11,16 L6,18 L2,10 Z"/>
      <path d="M22,22 L22,36 M22,22 Q25,20 26,24 L26,30"/>
    </svg>
    <h3>Pick Your Gear</h3>
    <p>We will help you choose your t-shirts, sweatshirts or other apparel items and determine sizes and quantities.</p>
  </div>
  <svg class="abs step-arrow" style="left:510px" width="44" height="10" viewBox="0 0 44 10" aria-hidden="true">
    <path d="M0,5 L42,5 M36,1 L42,5 L36,9" fill="none" stroke="var(--ink)" stroke-width="1.4"/>
  </svg>

  <div class="abs step" style="left:558px">
    <svg width="40" height="40" viewBox="0 0 40 40" fill="none" stroke="var(--red)" stroke-width="2" stroke-linecap="round" aria-hidden="true">
      <path d="M6,34 L30,6 L36,12 L10,38 L4,38 Z"/>
      <path d="M8,6 L34,34 M4,10 L10,4 L14,8 L8,14 Z"/>
    </svg>
    <h3>We Customize</h3>
    <p>We make the magic happen and our team of expert artists will design your shirts and get a proof out to you. Upon order</p>
  </div>

  <!-- footer -->
  <svg class="abs band-svg" style="top:1068px" height="24" viewBox="0 0 780 24" aria-hidden="true">
    <path d="M0,8 L60,16 L120,6 L180,14 L240,4 L300,14 L360,6 L420,16 L480,6 L540,14 L600,4 L660,14 L720,6 L780,12 L780,20 L700,14 L600,20 L500,12 L400,20 L300,12 L200,20 L100,12 L0,18 Z" fill="var(--tear-shadow)"/>
  </svg>

  <h2 class="abs cta display">We’d Love to Work With You!</h2>
  <div class="abs contact contact-phone">
    <span class="dot"><svg width="14" height="14" viewBox="0 0 24 24" aria-hidden="true"><path d="M6.6,10.8 a15,15 0 0,0 6.6,6.6 l2.2-2.2 a1,1 0 0,1 1-0.25 a11.4,11.4 0 0,0 3.6,0.6 a1,1 0 0,1 1,1 V20 a1,1 0 0,1 -1,1 A17,17 0 0,1 3,4 a1,1 0 0,1 1-1 h3.5 a1,1 0 0,1 1,1 a11.4,11.4 0 0,0 0.6,3.6 a1,1 0 0,1 -0.25,1 Z" fill="#fff"/></svg></span>
    <span>555-014-2290</span>
  </div>
  <div class="abs contact contact-email">
    <span class="dot"><svg width="14" height="14" viewBox="0 0 24 24" aria-hidden="true"><path d="M6.6,10.8 a15,15 0 0,0 6.6,6.6 l2.2-2.2 a1,1 0 0,1 1-0.25 a11.4,11.4 0 0,0 3.6,0.6 a1,1 0 0,1 1,1 V20 a1,1 0 0,1 -1,1 A17,17 0 0,1 3,4 a1,1 0 0,1 1-1 h3.5 a1,1 0 0,1 1,1 a11.4,11.4 0 0,0 0.6,3.6 a1,1 0 0,1 -0.25,1 Z" fill="#fff"/></svg></span>
    <span>avery@copperhollowtees.com</span>
  </div>

  <div class="abs badge" role="img" aria-label="Partner badge" style="left:462px;width:26px;border-radius:50%;background:#c7d3c0"></div>
  <div class="abs badge" role="img" aria-label="Certification badge" style="left:504px;width:26px;border-radius:50%;background:#e7a5a5"></div>
  <div class="abs badge" role="img" aria-label="Supplier listing badge" style="left:546px;width:56px;background:#cfc6e3"></div>
  <div class="abs badge" role="img" aria-label="Procurement listing badge" style="left:614px;width:46px;border-radius:13px;background:#b9cbe6"></div>
  <div class="abs badge" role="img" aria-label="Green travel badge" style="left:670px;width:36px;border-radius:50%;background:#b7d9a6"></div>
  <div class="abs badge" role="img" aria-label="Business association badge" style="left:718px;width:30px;background:#bcd4ee"></div>

  <div class="abs social" style="left:699px" role="img" aria-label="Social profile link"></div>
  <div class="abs social" style="left:722px" role="img" aria-label="Social profile link"></div>
  <div class="abs social" style="left:745px" role="img" aria-label="Social profile link"></div>

</main>
</body>
</html>
```